Sparrow Haulage needs a business card design.

Design a double-sided business card for new freight business. On the front, would like to see our logo along with the following info:

Martin Obuya
CEO/FOUNDER
555-206-7142
martinobuya@sparrow-haulage.example

On the reverse side, we would like to use the graphic image of our logo only without the Sparrow Haulage name.

```html
<!DOCTYPE html>
<html lang="en">
<head>
<meta charset="utf-8">
<title>Sparrow Haulage – Business Card</title>
<link href="https://fonts.googleapis.com/css2?family=Arimo:wght@400;700&display=swap" rel="stylesheet">
<style>
  :root {
    --page-bg: #2b2b2c;
    --card-bg: #1c1d1f;
    --brand-red: #c0090f;
    --brand-navy: #0c1470;
    --text-light: #d9d9d9;
    --rule: #6a6a6a;
    --pattern-a: #222325;
    --pattern-b: #1a1b1d;
  }
  * { margin: 0; padding: 0; box-sizing: border-box; }
  html, body {
    width: 1200px; height: 1108px; overflow: hidden;
    background: var(--page-bg);
    font-family: "Arimo", Arial, sans-serif;
  }
  .stage {
    position: relative; width: 1200px; height: 1108px;
    display: flex; justify-content: center; align-items: center; gap: 60px;
  }
  .card {
    position: relative; width: 400px; height: 660px;
    background: var(--card-bg);
    border-radius: 26px;
    box-shadow: 0 18px 40px rgba(0,0,0,.45);
    overflow: hidden;
  }
  .brand {
    position: absolute; left: 30px; right: 30px; top: 180px;
    display: flex; justify-content: center; align-items: center; gap: 12px;
  }
  .brand-mark {
    flex: none; width: 20px; height: 20px; background: var(--brand-red);
  }
  .brand-name {
    color: var(--brand-red); font-weight: 700; white-space: nowrap;
    font-size: 24px; letter-spacing: 2px; text-transform: uppercase;
  }
  .person {
    position: absolute; left: 0; right: 0; top: 392px; text-align: center;
  }
  .person-name {
    color: var(--brand-red); font-weight: 700; font-size: 27px;
    text-transform: uppercase; letter-spacing: .5px;
  }
  .person-title {
    margin-top: 8px; color: var(--text-light); font-size: 19px;
  }
  .icon-row {
    position: absolute; left: 30px; right: 30px; top: 478px;
    display: flex; align-items: center; gap: 10px;
  }
  .icon-row .rule { flex: 1; height: 1px; background: var(--rule); }
  .icon {
    width: 30px; height: 30px; border-radius: 4px; background: var(--brand-red);
    display: flex; align-items: center; justify-content: center;
  }
  .contact {
    position: absolute; left: 0; right: 0; top: 528px; text-align: center;
    color: var(--text-light); font-size: 17px; line-height: 26px;
  }
  .back-texture {
    position: absolute; inset: 0;
    background: linear-gradient(160deg, var(--pattern-a), var(--pattern-b) 70%);
  }
  .back-mark {
    position: absolute; left: 50%; bottom: 150px;
    width: 40px; height: 40px; margin-left: -20px;
    background: var(--brand-red);
  }
</style>
</head>
<body>
<main class="stage">
  <section class="card card-front">
    <div class="brand">
      <span class="brand-mark"></span>
      <span class="brand-name">Sparrow Haulage</span>
    </div>
    <div class="person">
      <div class="person-name">Martin Obuya</div>
      <div class="person-title">CEO/FOUNDER</div>
    </div>
    <div class="icon-row">
      <span class="rule"></span>
      <span class="icon" aria-label="phone">
        <svg width="18" height="18" viewBox="0 0 24 24"><path fill="#1c1d1f" d="M6.6 10.8a15.1 15.1 0 0 0 6.6 6.6l2.2-2.2a1 1 0 0 1 1-.25 11.4 11.4 0 0 0 3.6.57 1 1 0 0 1 1 1V20a1 1 0 0 1-1 1A17 17 0 0 1 3 4a1 1 0 0 1 1-1h3.5a1 1 0 0 1 1 1c0 1.25.2 2.45.57 3.57a1 1 0 0 1-.25 1z"/></svg>
      </span>
      <span class="icon" aria-label="email">
        <svg width="18" height="18" viewBox="0 0 24 24"><rect x="3" y="5" width="18" height="14" rx="1" fill="none" stroke="#1c1d1f" stroke-width="2"/><path d="M3 6l9 7 9-7" fill="none" stroke="#1c1d1f" stroke-width="2"/></svg>
      </span>
      <span class="icon" aria-label="website">
        <svg width="18" height="18" viewBox="0 0 24 24"><circle cx="12" cy="12" r="9" fill="none" stroke="#1c1d1f" stroke-width="2"/><path d="M3 12h18M12 3c3 3 3 15 0 18M12 3c-3 3-3 15 0 18" fill="none" stroke="#1c1d1f" stroke-width="1.6"/></svg>
      </span>
      <span class="rule"></span>
    </div>
    <div class="contact">
      <div class="contact-phone">555-206-7142</div>
      <div class="contact-email">martinobuya@sparrow-haulage.example</div>
      <div class="contact-web">www.sparrow-haulage.example</div>
    </div>
  </section>

  <section class="card card-back">
    <div class="back-texture" role="img" aria-label="Faint tone-on-tone repeating brand pattern across the card back"></div>
    <span class="back-mark" role="img" aria-label="Brand symbol"></span>
  </section>
</main>
</body>
</html>
```